Redesign Merle's RV Park & Lodge Website, Leeds, North Dakota

I need a totally re-designed website for my RV Park / Lodge. I want to not only provide information on my RV Park / Lodge, I want to provide my customers with information on the town and area attractions. I want to provide rate information. Ideally, I would like to have a button/page for each section: Welcome & Information, Area Attractions, Welcome to Leeds, Rates, Who's Merle?!, FAQ's and Where are we?. I don't know if this would be more expensive the more pages you have? If more pages is too expensive, then we can combine info on less pages. I want my logo included on the web page. I want Studio Flock to take down my old website and use the same address to put up my newly designed website.

Target Market(s)

Full time RVers, People who camp, hunt fish, People who recreate on Devils Lake, People who are looking for meeting/conference space, people who are looking for party venue

Industry/Entity Type

Accommodation

Number of Pages Required

3 page

Requirements
Must have
• I want a cozy, welcoming type web site. No super dark colors. Bright and cheerful.
• Must be simple and organized.
• NOTE: I have a file of pictures of the interior of Merle's Lodge that must be included in website. Please request this file if you will be designing my project as the files are too large to upload through Studio Flock.
Nice to have
• If you cannot open any of the files listed, please notify me.
Should not have
• No stark or super-formal designs.

```html
<!DOCTYPE html>
<html lang="en">
<head>
<meta charset="utf-8">
<title>Merle's RV Park &amp; Lodge · Leeds, North Dakota</title>
<link href="https://fonts.googleapis.com/css2?family=Lato:ital,wght@0,400;0,700;0,900;1,400&display=swap" rel="stylesheet">
<style>
:root{
  --green:#4b6a26;
  --olive-text:#3f5220;
  --maroon:#7a1e2b;
  --navy:#2d3c7c;
  --social-blue:#3b5a99;
  --ink:#333;
  --muted:#555;
  --rule:#d9d9d9;
  --grey-bg:#efefef;
  --white:#fff;
  --tick:#5a7a2a;
}
*{box-sizing:border-box;margin:0;padding:0}
html,body{width:1200px;height:3358px;overflow:hidden}
body{font-family:'Lato',sans-serif;color:var(--ink);background:var(--white);font-size:13px;line-height:1.6}
.page{position:relative;width:1200px;height:3358px}

/* header */
.site-header{height:130px;position:relative}
.brand{position:absolute;left:76px;top:30px;display:flex;align-items:center;gap:10px}
.brand-mark{flex:none;width:22px;height:22px;background:var(--maroon);border-radius:50%}
.brand-name{font-weight:700;font-size:12px;line-height:1.3;color:var(--ink);width:130px}
.social{position:absolute;left:632px;top:58px;display:flex;gap:22px}
.social span{width:18px;height:18px;border-radius:50%;background:#666}
.contact-top{position:absolute;left:880px;top:34px;font-size:13px}
.contact-top h4{font-size:12px;font-weight:700;color:var(--green);letter-spacing:.5px;margin-bottom:6px}
.contact-top p{display:flex;align-items:center;gap:14px;color:var(--navy);margin-bottom:2px}
.contact-top svg{width:14px;height:14px;fill:var(--green)}

/* nav */
.main-nav{height:53px;background:var(--green);display:flex;align-items:center;justify-content:space-between;padding:0 78px}
.main-nav a{color:var(--white);text-decoration:none;font-size:13px;letter-spacing:.3px}

/* hero */
.hero{height:562px;position:relative;background:linear-gradient(180deg,#9aa6b3 0%,#c4c9cd 40%,#8e8f8c 62%,#6d7a4e 80%,#8a8a6f 100%);text-align:center;color:var(--white)}
.hero-photo{position:absolute;inset:0}
.hero-inner{position:relative;padding-top:142px}
.hero h1{font-size:38px;font-weight:700;line-height:1.15;letter-spacing:.5px;text-shadow:0 1px 3px rgba(0,0,0,.4)}
.hero p{font-size:18px;line-height:1.5;margin:18px auto 0;width:840px;text-shadow:0 1px 3px rgba(0,0,0,.5)}
.btn-book{display:inline-block;margin-top:26px;background:var(--navy);color:var(--white);font-size:17px;padding:10px 36px;font-weight:700}
.dots{position:absolute;bottom:34px;left:0;right:0;display:flex;justify-content:center;gap:10px}
.dots span{width:9px;height:9px;border-radius:50%;background:var(--white);opacity:.85}

/* sections */
.section{text-align:center;padding:0 74px}
.section-title{font-size:32px;font-weight:700;color:var(--olive-text)}
.sub-title{font-size:17px;color:var(--navy);margin-top:18px}
.sub-title.maroon{color:var(--maroon);font-size:22px;font-weight:700;margin-top:20px}
.lead{font-size:13px;color:var(--ink);margin-top:6px;line-height:1.9}
.lodge{padding-top:48px}
.feature-row{display:flex;gap:56px;margin-top:40px;text-align:left}
.photo{flex:none;width:512px;height:294px}
.ticks{list-style:none;padding-top:4px}
.ticks li{position:relative;padding-left:34px;font-size:13.5px;margin-bottom:9px;line-height:1.5}
.ticks li svg{position:absolute;left:0;top:3px;width:15px;height:15px}
.divider{height:1px;background:var(--rule);margin:56px 74px 0}
.rvpark{padding-top:34px}
.note b{color:var(--maroon)}

.tents{margin-top:60px;height:123px;background:linear-gradient(90deg,#7d2633,#8e3440 50%,#7b2431);color:var(--white);text-align:center;padding-top:26px}
.tents h2{font-size:32px;font-weight:400}
.tents p{font-size:19px}

.reviews{padding-top:44px;text-align:center}
.reviews h2{font-size:31px;line-height:1.3;color:var(--olive-text);font-weight:700}
.btn-social{display:inline-flex;align-items:center;gap:10px;margin-top:26px;background:var(--social-blue);color:var(--white);font-weight:700;font-size:14px;padding:10px 30px}
.btn-social span{width:10px;height:10px;background:var(--white)}

.rates{margin-top:58px;height:608px;background:var(--grey-bg);padding-top:36px;text-align:center}
.rates h2{font-size:32px;color:var(--olive-text);font-weight:700}
.cards{display:flex;gap:29px;justify-content:center;margin-top:24px}
.card{width:331px;height:420px;background:var(--white)}
.card-head{height:167px;position:relative;display:flex;align-items:center;justify-content:center;color:var(--white);font-size:23px;line-height:1.2;text-shadow:0 1px 3px rgba(0,0,0,.5)}
.card-body{padding:22px 26px 0;font-size:13.5px;line-height:1.6}
.card-body strong{color:var(--maroon)}
.rates-note{margin-top:26px;font-style:italic;color:var(--olive-text);font-size:13.5px}

/* footer */
.site-footer{position:relative;height:230px}
.footer-brand{position:absolute;left:76px;top:30px}
.copyright{position:absolute;left:74px;top:158px;font-size:12px;color:var(--muted);line-height:1.6}
.fcol{position:absolute;top:28px;font-size:12px}
.fcol h4{color:var(--maroon);font-size:14px;font-weight:700;letter-spacing:.4px;margin-bottom:12px}
.fcol a{display:block;color:var(--muted);text-decoration:none;line-height:2.1}
.sitemap{left:334px}
.sitemap .cols{display:flex;gap:54px}
.address{left:624px}
.address p{display:flex;gap:14px;color:var(--muted);margin-bottom:8px;line-height:1.6}
.address svg{flex:none;width:13px;height:13px;fill:var(--green);margin-top:3px}
.signup{left:898px}
.signup .field{width:228px;height:34px;border:1px solid #bbb;padding:8px 12px;color:var(--ink)}
.signup .btn{display:inline-block;margin-top:12px;margin-left:138px;background:var(--navy);color:var(--white);font-size:13px;padding:8px 22px}
</style>
</head>
<body>
<div class="page">

<header class="site-header">
  <div class="brand"><span class="brand-mark"></span><span class="brand-name">Merle's RV Park &amp; Lodge<br>Leeds ND</span></div>
  <div class="social" aria-label="Social links"><span></span><span></span><span></span><span></span><span></span></div>
  <div class="contact-top">
    <h4>GET IN TOUCH:</h4>
    <p><svg viewBox="0 0 16 16"><path d="M3 1l3 3-2 2c1 2 3 4 5 5l2-2 3 3-2 3C7 14 2 9 1 3z"/></svg>701-555-0142, 701-555-0178</p>
    <p><svg viewBox="0 0 16 16"><path d="M1 3h14v10H1zM1 3l7 6 7-6"/></svg>stay@merlesrvpark.example</p>
  </div>
</header>

<nav class="main-nav">
  <a>HOME</a><a>WELCOME &amp; INFORMATION</a><a>AREA ATTRACTIONS</a><a>WELCOME TO LEEDS</a><a>RATES</a><a>WHO'S MERLE?!</a><a>FAQ'S</a><a>WHERE ARE WE</a>
</nav>

<section class="hero">
  <div class="hero-photo" role="img" aria-label="Photo of the red and grey lodge building on a prairie lawn under a cloudy sky"></div>
  <div class="hero-inner">
    <h1>WELCOME TO MERLE'S RV PARK &amp; LODGE<br>&amp; LEEDS, NORTH DAKOTA</h1>
    <p>Leeds is in the heart of some of the greatest hunting and fishing in the world. Merle's RV Park is located right on Highway 2 midway between Devils Lake and Rugby North Dakota.<br>We are smack dab in the middle of it all!</p>
    <span class="btn-book">BOOK NOW</span>
  </div>
  <div class="dots"><span></span><span></span><span></span><span></span></div>
</section>

<section class="section lodge">
  <h2 class="section-title">Merle's Lodge</h2>
  <p class="sub-title">Are you looking for a cozy, but spacious home away from home?</p>
  <p class="lead">Well, you have found it! Merle's Lodge is 2200 square feet of living space. There are 2 spacious bedrooms with queen sized beds and another common sleeping area with 5 sets of bunk beds. Available to you are 2 restrooms with showers, a great room with dining and relaxing space and a full kitchen.<br>Everything is supplied for you: towels, bedding, cookware, dishware, grill and etc...all that you need to make your stay worry and hassle free.<br>Throw some clothes in a suitcase, hit the road and we will have your home away from home all ready when you get here!<br>The Lodge is open all year round.</p>
  <h3 class="sub-title maroon">Meeting / Conference Space</h3>
  <p class="lead">Are you looking for a venue for your next meeting, training event, guys/girls weekend, quilt retreat, holiday gathering, family reunion, birthday, wedding party or get-together? We've got you covered! Merle's Lodge seats about 65 people comfortably. Many of our customers have commented that Merle's was the perfect place for their event because it was so inviting...and just like home!</p>
  <div class="feature-row">
    <div class="photo" role="img" aria-label="Photo of the lodge great room set with dining tables and chairs" style="background:linear-gradient(135deg,#a88a5e,#d9c9a8 45%,#8f6b4a)"></div>
    <ul class="ticks">
      <li><svg viewBox="0 0 16 16"><circle cx="8" cy="8" r="8" fill="var(--tick)"/><path d="M4.5 8.3l2.3 2.2 4.7-4.8" stroke="#fff" stroke-width="1.8" fill="none"/></svg>Groups – hunting, fishing, working, playing</li>
      <li><svg viewBox="0 0 16 16"><circle cx="8" cy="8" r="8" fill="var(--tick)"/><path d="M4.5 8.3l2.3 2.2 4.7-4.8" stroke="#fff" stroke-width="1.8" fill="none"/></svg>2200 square feet</li>
      <li><svg viewBox="0 0 16 16"><circle cx="8" cy="8" r="8" fill="var(--tick)"/><path d="M4.5 8.3l2.3 2.2 4.7-4.8" stroke="#fff" stroke-width="1.8" fill="none"/></svg>Full kitchen</li>
      <li><svg viewBox="0 0 16 16"><circle cx="8" cy="8" r="8" fill="var(--tick)"/><path d="M4.5 8.3l2.3 2.2 4.7-4.8" stroke="#fff" stroke-width="1.8" fill="none"/></svg>Free WiFi</li>
      <li><svg viewBox="0 0 16 16"><circle cx="8" cy="8" r="8" fill="var(--tick)"/><path d="M4.5 8.3l2.3 2.2 4.7-4.8" stroke="#fff" stroke-width="1.8" fill="none"/></svg>Satellite TV</li>
      <li><svg viewBox="0 0 16 16"><circle cx="8" cy="8" r="8" fill="var(--tick)"/><path d="M4.5 8.3l2.3 2.2 4.7-4.8" stroke="#fff" stroke-width="1.8" fill="none"/></svg>2 restrooms, one is handicap accessible</li>
      <li><svg viewBox="0 0 16 16"><circle cx="8" cy="8" r="8" fill="var(--tick)"/><path d="M4.5 8.3l2.3 2.2 4.7-4.8" stroke="#fff" stroke-width="1.8" fill="none"/></svg>Sleeps 14 – 2 bedrooms with queen sized beds, plus a shared sleeping area with bunk beds</li>
      <li><svg viewBox="0 0 16 16"><circle cx="8" cy="8" r="8" fill="var(--tick)"/><path d="M4.5 8.3l2.3 2.2 4.7-4.8" stroke="#fff" stroke-width="1.8" fill="none"/></svg>A great room with ample seating for large groups</li>
      <li><svg viewBox="0 0 16 16"><circle cx="8" cy="8" r="8" fill="var(--tick)"/><path d="M4.5 8.3l2.3 2.2 4.7-4.8" stroke="#fff" stroke-width="1.8" fill="none"/></svg>Merle's supplies everything...bedding, towels, cookware, etc.</li>
      <li><svg viewBox="0 0 16 16"><circle cx="8" cy="8" r="8" fill="var(--tick)"/><path d="M4.5 8.3l2.3 2.2 4.7-4.8" stroke="#fff" stroke-width="1.8" fill="none"/></svg>Kids stay free.</li>
    </ul>
  </div>
</section>

<div class="divider"></div>

<section class="section rvpark">
  <h2 class="section-title">Merle's RV Park</h2>
  <p class="lead" style="margin-top:14px">Merle's RV Park sits right next to Highway 2 on the north side. We have 14 full service spaces –sewer, water and electric (20, 30, 50 amp). There is an indoor restroom with shower that is available 24 hours a day to our RV customers. Plenty of space is available to you for parking boats, trailers, etc.<br>Merle's RV Park year round, but water usage depends on when spring thaw and freeze up occurs.</p>
  <p class="lead note"><b>Please note:</b> Merle's RV Park is an unattended RV park. No reservations required. Please pull on in, use our self-service check-in and then sit back and relax!</p>
  <div class="feature-row" style="margin-top:28px;gap:40px">
    <ul class="ticks" style="width:504px">
      <li><svg viewBox="0 0 16 16"><circle cx="8" cy="8" r="8" fill="var(--tick)"/><path d="M4.5 8.3l2.3 2.2 4.7-4.8" stroke="#fff" stroke-width="1.8" fill="none"/></svg>14 Full Service Sites</li>
      <li><svg viewBox="0 0 16 16"><circle cx="8" cy="8" r="8" fill="var(--tick)"/><path d="M4.5 8.3l2.3 2.2 4.7-4.8" stroke="#fff" stroke-width="1.8" fill="none"/></svg>Electric (20, 30 &amp; 50amp), Water, Sewer</li>
      <li><svg viewBox="0 0 16 16"><circle cx="8" cy="8" r="8" fill="var(--tick)"/><path d="M4.5 8.3l2.3 2.2 4.7-4.8" stroke="#fff" stroke-width="1.8" fill="none"/></svg>Free WiFi</li>
      <li><svg viewBox="0 0 16 16"><circle cx="8" cy="8" r="8" fill="var(--tick)"/><path d="M4.5 8.3l2.3 2.2 4.7-4.8" stroke="#fff" stroke-width="1.8" fill="none"/></svg>Safe &amp; convenient location</li>
      <li><svg viewBox="0 0 16 16"><circle cx="8" cy="8" r="8" fill="var(--tick)"/><path d="M4.5 8.3l2.3 2.2 4.7-4.8" stroke="#fff" stroke-width="1.8" fill="none"/></svg>24 hour indoor restroom with shower</li>
      <li><svg viewBox="0 0 16 16"><circle cx="8" cy="8" r="8" fill="var(--tick)"/><path d="M4.5 8.3l2.3 2.2 4.7-4.8" stroke="#fff" stroke-width="1.8" fill="none"/></svg>Meadowlark Camper Circle accepted for first night</li>
      <li><svg viewBox="0 0 16 16"><circle cx="8" cy="8" r="8" fill="var(--tick)"/><path d="M4.5 8.3l2.3 2.2 4.7-4.8" stroke="#fff" stroke-width="1.8" fill="none"/></svg>Ample room to park boats, trailers etc.</li>
      <li><svg viewBox="0 0 16 16"><circle cx="8" cy="8" r="8" fill="var(--tick)"/><path d="M4.5 8.3l2.3 2.2 4.7-4.8" stroke="#fff" stroke-width="1.8" fill="none"/></svg>Convenience store/gas station located right across the street. Restaurant onsite.</li>
      <li><svg viewBox="0 0 16 16"><circle cx="8" cy="8" r="8" fill="var(--tick)"/><path d="M4.5 8.3l2.3 2.2 4.7-4.8" stroke="#fff" stroke-width="1.8" fill="none"/></svg>Merle's operates on a first come, first serve basis for short term stays. If you would like to reserve for a stay longer than 3 days, please call Merle.</li>
    </ul>
    <div class="photo" role="img" aria-label="Photo of a camper trailer and tents parked on green grass beneath trees" style="width:510px;height:293px;background:linear-gradient(180deg,#4a8ad0 0%,#7fb4e0 30%,#5f8a3a 60%,#6fa33d 100%)"></div>
  </div>
</section>

<section class="tents" role="img" aria-label="Banner photo of tent sites tinted red">
  <h2>Tents</h2>
  <p>Primitive &amp; tent sites are also available.</p>
</section>

<section class="reviews">
  <h2>What our customers are saying about<br>Merle's RV Park &amp; Lodge</h2>
  <span class="btn-social"><span></span>Check Out Our Social Page</span>
</section>

<section class="rates">
  <h2>Rates</h2>
  <div class="cards">
    <article class="card">
      <div class="card-head" role="img" aria-label="Darkened photo of the lodge building" style="background:linear-gradient(180deg,#4d4f55,#5a4044 60%,#3f4a30)">Merle's Lodge<br>Pricing</div>
      <div class="card-body"><strong>$200 for 24 hours.</strong><br>The first 6 adults are included in the $200 per night rent. Each adult exceeding the initial 6, must pay $25 per night. Kids under age 16 stay free.</div>
    </article>
    <article class="card">
      <div class="card-head" role="img" aria-label="Darkened photo of a camper trailer on the lawn" style="background:linear-gradient(180deg,#3c5a78,#5f6f5a 55%,#3e5a2a)">Merle's RV Park<br>Pricing</div>
      <div class="card-body"><strong>RV Sites:</strong>$24/Night $125/Week $375/month<br>This price is for 4 adults. Any adults exceeding the initial 4, must pay $5 extra per night. Kids under 16 stay free.<br><strong>Tent Sites:</strong> $12/Night<br>This price is for 4 adults. Any adults exceeding the initial 4, must pay $3 extra per night. Kids under 16 stay free.</div>
    </article>
    <article class="card">
      <div class="card-head" role="img" aria-label="Darkened photo of the shower room" style="background:linear-gradient(90deg,#6b5030,#a08058 40%,#5a4a3a)">Showers</div>
      <div class="card-body">Showers are $5 per person for unregistered customers. There is no charge for anyone that uses the shower that is staying at Merle's RV Park &amp; Lodge.</div>
    </article>
  </div>
  <p class="rates-note">Meadowlark Camper Circle accepted for the first night.</p>
</section>

<footer class="site-footer">
  <div class="brand footer-brand"><span class="brand-mark"></span><span class="brand-name">Merle's RV Park &amp; Lodge<br>Leeds ND</span></div>
  <p class="copyright">Copyright © 2018 Company Name<br>All Right Reserved</p>
  <div class="fcol sitemap">
    <h4>SITE MAP</h4>
    <div class="cols">
      <div><a>Home</a><a>Welcome &amp; Information</a><a>Area Attractions</a><a>Welcome to Leeds</a><a>Rates</a></div>
      <div><a>Who's Merle?!</a><a>FAQ's</a><a>Where are we</a></div>
    </div>
  </div>
  <div class="fcol address">
    <h4>CONTACT ADDRESS</h4>
    <p><svg viewBox="0 0 16 16"><path d="M8 0a5 5 0 015 5c0 4-5 11-5 11S3 9 3 5a5 5 0 015-5zm0 3a2 2 0 100 4 2 2 0 000-4z"/></svg>120 Prairie Ave Leeds<br>ND 58000</p>
    <p><svg viewBox="0 0 16 16"><path d="M3 1l3 3-2 2c1 2 3 4 5 5l2-2 3 3-2 3C7 14 2 9 1 3z"/></svg>701-555-0142, 701-555-0178</p>
    <p><svg viewBox="0 0 16 16"><path d="M1 3h14v10H1z"/></svg>stay@merlesrvpark.example</p>
  </div>
  <div class="fcol signup">
    <h4>EMAIL SIGN UP</h4>
    <div class="field">Enter Email Address</div>
    <span class="btn">SIGN UP</span>
  </div>
</footer>

</div>
</body>
</html>
```